Stickers By Dwayne needs a website and logo design

I am starting a home business, "Stickers By Dwayne", which I will sell car decals/decals of some sort. I am looking for a creative and professional looking website. I do not want anything too plain/bland, or else I could design it myself. I am up for many options, when it comes to text/colors, and I am not opposed to much. Just nothing too plain. Currently have no logo design to use, may also add this to the project as well. ( I use Wordpress for my site server so it has to be compatible to be used with that website.
Also, I make decals that mainly go on car windows, not as big on car body’s. Also put decals on glassware, and other items. But mainly car windows

• some color, not be bland and white everywhere.

```html
<!DOCTYPE html>
<html lang="en">
<head>
<meta charset="utf-8">
<title>Stickers By Dwayne</title>
<link href="https://fonts.googleapis.com/css2?family=Roboto:wght@400;500;700&display=swap" rel="stylesheet">
<style>
:root{
  --black:#000;
  --ink:#0b0b0b;
  --panel:#111;
  --yellow:#fdb813;
  --red:#fe3e12;
  --green:#6cad0a;
  --muted:#9a9a9a;
  --line:#2a2a2a;
  --white:#fff;
}
*{box-sizing:border-box;margin:0;padding:0}
html,body{width:784px;height:1200px;overflow:hidden;background:var(--black);font-family:'Roboto',sans-serif;color:var(--white)}
.page{position:relative;width:784px;height:1200px;overflow:hidden}
.abs{position:absolute}
.header{left:0;top:0;width:784px;height:63px;background:var(--black)}
.search{left:106px;top:22px;width:114px;height:20px;border:1px solid #444;font-size:6px;color:#777;padding:6px 8px}
.search svg{position:absolute;right:7px;top:5px}
.brand{left:0;width:784px;top:20px;text-align:center;font-weight:700;font-size:20px;color:var(--yellow)}
.icons{left:596px;top:25px;display:flex;gap:11px}
.nav{left:0;top:63px;width:784px;height:32px;background:var(--yellow)}
.nav ul{list-style:none;display:flex;position:absolute;left:104px;top:0;height:32px}
.nav li{font-size:7px;font-weight:500;text-transform:uppercase;line-height:32px;margin-right:31px}
.nav li.active{background:var(--black);padding:0 12px;margin-right:24px}
.hero{left:0;top:95px;width:784px;height:291px;background:radial-gradient(ellipse at 60% 45%,#3b3b3b 0%,#151515 55%,#050505 100%)}
.hero-photo{left:300px;top:35px;width:470px;height:230px;border-radius:40% 50% 20% 20%;background:radial-gradient(ellipse at 50% 50%,#e9e9e9 0%,#9a9a9a 45%,rgba(40,40,40,0) 72%)}
.hero h1{left:105px;top:98px;font-size:20px;font-weight:500}
.hero p{left:105px;top:132px;width:175px;font-size:7px;line-height:12.6px;color:#bbb}
.btn{left:105px;top:182px;width:63px;height:23px;background:var(--yellow);font-size:7px;text-align:center;line-height:23px}
.dots{left:624px;top:266px;display:flex;gap:4px;align-items:center}
.dots span{width:5px;height:5px;border-radius:50%;background:#fff}
.dots span.on{width:10px;height:10px;border:2px solid var(--yellow);background:#fff}
.band{left:0;top:386px;width:784px;height:312px;background:linear-gradient(#1c1c1c 0,#050505 60px,#000 100%)}
.features{left:106px;top:390px;display:flex}
.feature{width:190px;height:117px;text-align:center;border-top:5px solid rgba(0,0,0,.15);padding-top:14px}
.feature.car{background:var(--yellow)}
.feature.install{background:var(--red)}
.feature.shop{background:var(--green)}
.feature h3{font-size:9.5px;font-weight:500;margin-top:10px}
.feature p{font-size:6.6px;line-height:12.6px;margin-top:8px;padding:0 14px}
.about h2{left:105px;top:542px;font-size:15px;font-weight:400}
.about p{left:106px;top:571px;width:315px;font-size:6.7px;line-height:12.8px;color:#aaa}
.about-photo{left:463px;top:534px;width:215px;height:127px;background:linear-gradient(90deg,#f2f2f2,#e6c232 35%,#dde2ea 65%,#f2f2f2)}
.products{left:0;top:698px;width:784px;height:298px;background:linear-gradient(#1b1b1b,#0c0c0c)}
.tab{left:302px;top:698px}
.tab span{position:absolute;left:0;width:180px;top:8px;text-align:center;font-size:14px}
.cards{left:105px;top:760px;display:flex;gap:3px}
.card{width:141px;height:180px;background:var(--black);position:relative}
.card .art{position:absolute;left:36px;top:20px;width:70px;height:70px;border-radius:50%}
.card h4{position:absolute;top:112px;width:100%;text-align:center;font-size:10px;font-weight:400}
.card p{position:absolute;top:129px;width:100%;text-align:center;font-size:7px;color:var(--muted)}
.card .price{position:absolute;left:0;top:150px;width:100%;height:30px;border-top:1px solid #262626;display:flex}
.price b{width:70px;text-align:center;line-height:30px;font-size:8px;font-weight:500;border-right:1px solid #262626}
.price i{flex:1;display:flex;align-items:center;justify-content:center}
.footer{left:0;top:996px;width:784px;height:204px;background:#050505}
.col{top:1026px}
.col h5{font-size:10px;font-weight:500;color:var(--yellow);margin-bottom:14px}
.col li{list-style:none;font-size:7px;color:#bbb;line-height:14.8px}
.divider{top:1028px;width:1px;height:106px;background:#222}
.contact{left:553px;display:flex;align-items:center;gap:9px;font-size:7px;color:#bbb;line-height:11.5px}
.contact .ring{width:21px;height:21px;border:1px solid #666;border-radius:50%;display:flex;align-items:center;justify-content:center;flex:none}
.rule{left:0;top:1167px;width:784px;height:1px;background:#1e1e1e}
.social{left:106px;top:1181px;display:flex;gap:6px}
.social span{width:4px;height:4px;border-radius:50%;background:#fff}
.copy{left:502px;top:1179px;font-size:7px;color:#ddd}
</style>
</head>
<body>
<div class="page">
  <header class="abs header"></header>
  <div class="abs search">Enter a keyword...
    <svg width="7" height="7" viewBox="0 0 10 10"><circle cx="4" cy="4" r="3" fill="none" stroke="#fdb813" stroke-width="1.5"/><line x1="6.3" y1="6.3" x2="9" y2="9" stroke="#fdb813" stroke-width="1.5"/></svg>
  </div>
  <div class="abs brand">Stickers By Dwayne</div>
  <div class="abs icons">
    <svg width="12" height="12" viewBox="0 0 12 12" fill="none" stroke="#ddd"><circle cx="6" cy="4" r="2.5"/><path d="M1.5 11.5c0-3 2-4.5 4.5-4.5s4.5 1.5 4.5 4.5z"/></svg>
    <svg width="13" height="12" viewBox="0 0 13 12" fill="none" stroke="#ddd"><path d="M6.5 11 1.6 6.2A2.9 2.9 0 0 1 6.5 2.2a2.9 2.9 0 0 1 4.9 4z"/></svg>
    <svg width="14" height="12" viewBox="0 0 14 12" fill="none" stroke="#ddd"><path d="M.5 1h2l1.8 7h7l1.7-5H3.4"/><circle cx="5" cy="10.5" r="1"/><circle cx="10" cy="10.5" r="1"/></svg>
    <svg width="11" height="12" viewBox="0 0 11 12" fill="none" stroke="#ddd"><rect x="1" y="5" width="9" height="6.5"/><path d="M3 5V3.5a2.5 2.5 0 0 1 5 0V5"/></svg>
  </div>
  <nav class="abs nav">
    <ul>
      <li class="active">Home</li><li>All Products</li><li>Installation</li><li>Shop</li><li>Sticker Catalogue</li><li>Accessories</li><li>Blog</li><li>Contact</li>
    </ul>
  </nav>

  <section class="abs hero">
    <div class="abs hero-photo" role="img" aria-label="White race car with livery and number decals in a dark studio"></div>
    <h1 class="abs">Stickers By Dwayne</h1>
    <p class="abs">Sed ut perspiciatis unde omnis iste natus error sit voluptatem accusantium doloremque laudantiu m, totam rem aperiam, eaque ipsa quae.</p>
    <div class="abs btn">Read More</div>
    <div class="abs dots"><span class="on"></span><span></span><span></span><span></span></div>
  </section>

  <section class="abs band"></section>
  <div class="abs features">
    <div class="feature car">
      <svg width="70" height="28" viewBox="0 0 70 28" fill="none" stroke="#fff" stroke-width="1.2"><path d="M3 20V14l8-2 10-8h22l12 8 10 2v6h-5M12 20H3m54 0H19"/><circle cx="15" cy="20" r="4"/><circle cx="53" cy="20" r="4"/><path d="M23 11l4-5h12v5zM42 6h2l8 5H42z"/></svg>
      <h3>CAR DECALS</h3>
      <p>Sed ut perspiciatis unde omnis iste natus er sitv oluptatem accusantium doloremqueud.</p>
    </div>
    <div class="feature install">
      <svg width="36" height="36" viewBox="0 0 36 36" fill="none" stroke="#fff" stroke-width="1.2"><path d="M22 4a8 8 0 0 0-7 11L4 26a3 3 0 0 0 4 4l11-11a8 8 0 0 0 11-7l-5 3-4-2-1-4z"/><circle cx="7" cy="27" r="1"/></svg>
      <h3>INSTALLATION</h3>
      <p>Sed ut perspiciatis unde omnis iste natus er sitv oluptatem accusantium doloremqueud.</p>
    </div>
    <div class="feature shop">
      <svg width="36" height="36" viewBox="0 0 36 36" fill="none" stroke="#fff" stroke-width="1.2"><path d="M4 11h28l-4 22H8z"/><path d="M12 14V8a6 6 0 0 1 12 0v6"/></svg>
      <h3>SHOP</h3>
      <p>Sed ut perspiciatis unde omnis iste natus er sitv oluptatem accusantium doloremqueud.</p>
    </div>
  </div>

  <div class="about">
    <h2 class="abs">About Stickers By Dwayne</h2>
    <p class="abs">Sed ut perspiciatis unde omnis iste natus error sit voluptatem accusantium doloremque laud antium, totam rem aperiam, eaque ipsa quae ab illo inventore veritatis et qua.Sarchitecto bea tae vitae dicta sunt explicabo. Nemo enim ipsam voluptatem quia voluptas sit aspernatur aut odit aut fugit, sed quia consequuntur magni dolores eos qui ratione voluptatem sequi nesciue porro quisquam est, qui dolorem ipsodit aut fugit, sed quia consequuntur magni dolores eos qui ratione voluptatem sequi nesciue porro quisquam est, qui dolorem ipsu.</p>
    <div class="abs about-photo" role="img" aria-label="Two stock cars, yellow and white, with racing number decals"></div>
  </div>

  <section class="abs products"></section>
  <div class="abs tab">
    <svg width="180" height="33" viewBox="0 0 180 33"><polygon points="0,0 180,0 160,33 20,33" fill="#fdb813"/></svg>
    <span>Top Products</span>
  </div>
  <svg class="abs" style="left:72px;top:832px" width="14" height="36" viewBox="0 0 14 36" fill="none" stroke="#888"><path d="M13 1 1 18l12 17"/></svg>
  <svg class="abs" style="left:695px;top:832px" width="14" height="36" viewBox="0 0 14 36" fill="none" stroke="#888"><path d="M1 1l12 17L1 35"/></svg>
  <div class="abs cards">
    <div class="card"><div class="art" role="img" aria-label="Racing badge decal" style="background:radial-gradient(#fff,#d93030 60%,#000 72%)"></div><h4>Product Name</h4><p>Sed ut perspiciatis unde omnis</p><div class="price"><b>£ 65.00</b><i><svg width="16" height="13" viewBox="0 0 14 12" fill="none" stroke="#fdb813"><path d="M.5 1h2l1.8 7h7l1.7-5H3.4"/><circle cx="5" cy="10.5" r="1"/><circle cx="10" cy="10.5" r="1"/></svg></i></div></div>
    <div class="card"><div class="art" role="img" aria-label="Flame decal" style="border-radius:40%;background:radial-gradient(ellipse,#ffd23a,#e8421a 55%,#000 72%)"></div><h4>Product Name</h4><p>Sed ut perspiciatis unde omnis</p><div class="price"><b>£ 65.00</b><i><svg width="16" height="13" viewBox="0 0 14 12" fill="none" stroke="#fdb813"><path d="M.5 1h2l1.8 7h7l1.7-5H3.4"/><circle cx="5" cy="10.5" r="1"/><circle cx="10" cy="10.5" r="1"/></svg></i></div></div>
    <div class="card"><div class="art" role="img" aria-label="Winged letter decal" style="background:radial-gradient(#d32020,#ffffff 45%,#000 72%)"></div><h4>Product Name</h4><p>Sed ut perspiciatis unde omnis</p><div class="price"><b>£ 65.00</b><i><svg width="16" height="13" viewBox="0 0 14 12" fill="none" stroke="#fdb813"><path d="M.5 1h2l1.8 7h7l1.7-5H3.4"/><circle cx="5" cy="10.5" r="1"/><circle cx="10" cy="10.5" r="1"/></svg></i></div></div>
    <div class="card"><div class="art" role="img" aria-label="Red winged piston emblem decal" style="background:radial-gradient(#2a2a2a,#d42222 45%,#000 72%)"></div><h4>Product Name</h4><p>Sed ut perspiciatis unde omnis</p><div class="price"><b>£ 65.00</b><i><svg width="16" height="13" viewBox="0 0 14 12" fill="none" stroke="#fdb813"><path d="M.5 1h2l1.8 7h7l1.7-5H3.4"/><circle cx="5" cy="10.5" r="1"/><circle cx="10" cy="10.5" r="1"/></svg></i></div></div>
  </div>

  <footer class="abs footer"></footer>
  <div class="abs col" style="left:105px"><h5>INFORMATION</h5><ul><li>About us</li><li>Order History</li><li>Custom Service</li><li>Dynamicus</li><li>Terms &amp; Condition</li><li>Order History</li></ul></div>
  <div class="abs divider" style="left:215px"></div>
  <div class="abs col" style="left:262px"><h5>LINKS</h5><ul><li>Specials Products</li><li>Site Map</li><li>Sed ut perspiciatis</li><li>Gunde omnis ist</li><li>Sit voluptatem</li><li>Ntiumem</li></ul></div>
  <div class="abs divider" style="left:367px"></div>
  <div class="abs col" style="left:411px"><h5>PRODUCTS</h5><ul><li>Sed ut perspiciatis</li><li>Gunde omnis iste natus</li><li>Sit voluptatem accus</li><li>Ntium dolorem</li><li>Hue laudantium</li></ul></div>
  <div class="abs divider" style="left:520px"></div>
  <div class="abs col" style="left:553px"><h5>CONTACTS</h5></div>
  <div class="abs contact" style="top:1048px"><span class="ring"><svg width="7" height="9" viewBox="0 0 8 10" fill="none" stroke="#ddd"><path d="M4 9.5S1 6 1 4a3 3 0 0 1 6 0c0 2-3 5.5-3 5.5z"/><circle cx="4" cy="4" r="1"/></svg></span><span>1420 W. Harbor Ln., Unit B,<br>Sample City, AZ 85000</span></div>
  <div class="abs contact" style="top:1075px"><span class="ring"><svg width="8" height="8" viewBox="0 0 10 10" fill="#ddd"><path d="M2 .5 4 3 3 4.2a6 6 0 0 0 2.8 2.8L7 6l2.5 2L8.3 9.5C4 9 1 6 .5 1.7z"/></svg></span><span style="font-size:8px">Phone: 555.014.2290</span></div>
  <div class="abs contact" style="top:1100px"><span class="ring"><svg width="8" height="6" viewBox="0 0 10 7" fill="#ddd"><path d="M0 0h10L5 4zM0 1.2l5 3.8 5-3.8V7H0z"/></svg></span><span style="font-size:8px">hello@stickersbydwayne.example</span></div>

  <div class="abs rule"></div>
  <div class="abs social"><span></span><span></span><span></span><span></span><span></span><span></span></div>
  <div class="abs copy">Copyright © 2017 Stickers By Dwayne. All Rights Reserved.</div>
</div>
</body>
</html>
```